Life Coaching business needs a new flyer

We are an Australian business that specialises in Life Coaching, Career Coaching, Health and Wellness Coaching, Yoga and Pilates. We need a A4 double sided flyer that is full colour and folded to DL format. I have attached a couple of designs that I like and some pictures and would like the flyer to be bright yet stylish.

Industry/Entity Type

Life Coaching

```html
<!DOCTYPE html>
<html lang="en">
<head>
<meta charset="utf-8">
<title>Brightpath Coaching &amp; Meditation Studio – DL Flyer</title>
<link rel="stylesheet" href="https://fonts.googleapis.com/css2?family=Open+Sans:ital,wght@0,400;0,600;0,700;1,400&family=Lora:wght@600;700&family=Pinyon+Script&display=swap">
<style>
:root{
  --bg:#bdbdbd;
  --paper:#ffffff;
  --teal:#1f8fbf;
  --blue:#1b8fd9;
  --blue-deep:#0f6fb8;
  --blue-light:#e4f1fa;
  --green:#3fa82f;
  --ink:#2b2b2b;
  --white:#ffffff;
}
*{box-sizing:border-box;margin:0;padding:0}
html,body{width:1034px;height:1200px;overflow:hidden}
body{background:var(--bg);font-family:"Open Sans",Arial,sans-serif;color:var(--ink)}
.canvas{width:1034px;height:1200px;display:flex;flex-direction:column;align-items:center;justify-content:space-evenly}
.sheet{position:relative;width:806px;height:570px;background:var(--paper);display:grid;grid-template-columns:repeat(3,1fr);box-shadow:0 6px 18px rgba(0,0,0,.25);overflow:hidden}
.panel{position:relative;overflow:hidden}
.panel + .panel{border-left:1px solid rgba(0,0,0,.06)}
.shape{position:absolute;inset:0;width:100%;height:100%}
.photo{position:absolute;left:0;right:0}
.content{position:relative;z-index:2}
.heading{font-family:"Lora",Georgia,serif;font-weight:700;color:var(--teal);font-size:15px;line-height:1.2}
.body-text{font-size:8.6px;line-height:1.5}
.body-text p{margin-bottom:7px}
.brand{font-family:"Lora",Georgia,serif;font-weight:600;display:flex;align-items:center;gap:7px}
.brand-dot{width:14px;height:14px;border-radius:50%;flex:none}

/* outside: testimonials */
.testimonials .content{padding:26px 20px 0}
.testimonials .heading{margin-bottom:9px}
.testimonials .photo{bottom:0;height:165px;background:linear-gradient(180deg,#3b86d0 0%,#7fb6e6 60%,#f3c7a0 100%)}

/* outside: contact */
.contact{background:linear-gradient(180deg,var(--blue) 0%,#2a9ae0 55%,var(--blue-deep) 100%);color:var(--white)}
.contact .intro{font-size:8.2px;line-height:1.5;padding:24px 22px 0}
.contact .intro p{margin-bottom:8px}
.contact .brand{justify-content:center;color:var(--white);font-size:15px;margin-top:22px}
.contact .brand-dot{background:var(--white)}
.contact .details{text-align:center;margin-top:12px;font-family:"Lora",Georgia,serif}
.contact .details h3{font-size:17px;font-weight:700;margin-bottom:4px}
.contact .details p{font-size:10.5px;font-weight:600;line-height:1.45}
.contact .photo{top:300px;height:180px;background:linear-gradient(180deg,#8a7566 0%,#5b4a40 55%,#2e2623 100%)}
.contact .offer{position:absolute;left:0;right:0;bottom:0;height:96px;background:var(--green);z-index:2;display:flex;align-items:center;justify-content:center;text-align:center;font-family:"Lora",Georgia,serif;font-weight:700;font-size:11.5px;line-height:1.45;padding:0 12px}

/* outside: cover */
.cover{background:linear-gradient(180deg,#ffffff 0%,var(--blue-light) 100%)}
.cover .brand{position:absolute;top:34px;left:0;right:0;justify-content:center;color:var(--teal);font-size:17px;z-index:2}
.cover .brand-dot{background:var(--green)}
.cover .services{position:absolute;right:26px;bottom:58px;z-index:2;text-align:right;font-family:"Pinyon Script",cursive;color:var(--white);font-size:31px;line-height:1.35}

/* inside: intro */
.questions .content{padding:30px 20px 0}
.questions .asks{font-size:9.8px;font-weight:700;line-height:1.4;color:#111}
.questions .asks p{margin-bottom:8px}
.questions .heading{margin:14px 0 8px}
.questions .photo{bottom:0;height:135px;background:linear-gradient(180deg,#1f7fd0 0%,#5aa8e6 55%,#e9f3fb 100%)}

/* inside: services */
.services-panel .content{padding:30px 20px 0}
.services-panel .heading{margin-bottom:6px}
.services-panel .heading + .body-text{margin-bottom:10px}
.services-panel .brand{color:var(--teal);font-size:14px;margin-top:12px;justify-content:center}
.services-panel .brand-dot{background:var(--green)}
.services-panel .photo{bottom:0;height:165px;background:linear-gradient(120deg,#f2b86a 0%,#e38d47 45%,#9a5a2e 100%)}

/* inside: wellness */
.wellness{background:linear-gradient(180deg,#ffffff 0%,#f1f6fa 100%)}
.wellness .content{padding:30px 20px 0}
.wellness .heading{margin-bottom:6px}
.wellness .heading + .body-text{margin-bottom:10px}
.tick-list{list-style:none;font-size:8.6px;font-style:italic;line-height:1.55;margin-top:6px;width:180px}
.tick-list li{display:flex;gap:6px;align-items:flex-start}
.tick-list svg{flex:none;margin-top:2px}
.wellness .offerings{position:absolute;right:18px;left:30px;bottom:20px;z-index:2;text-align:right;color:var(--white)}
.wellness .offerings h4{font-family:"Lora",Georgia,serif;font-size:13px;font-weight:700;margin-bottom:3px}
.wellness .offerings p{font-size:8.4px;line-height:1.5;margin-bottom:9px}
</style>
</head>
<body>
<main class="canvas">

  <section class="sheet sheet-outside" aria-label="Flyer outside">

    <article class="panel testimonials">
      <div class="content">
        <h2 class="heading">Happy Clients Testimonials</h2>
        <div class="body-text">
          <p>“I have lost 10 kilos and now have the energy to play with my kids. Thanks Jess for your support, guidance and helping me get rid of my limiting beliefs. I feel I can achieve anything now! The sky’s the limit” Mia, Mosman</p>
          <p>“I had always wanted to start up own café however every time it came to putting it into practice I would procrastinate and not achieve anything. I become overwhelmed with the whole process and never achieved anything. Jess put it into bite sized chunks and helped me to set small achievable goals. I am now a happy café owner.” Tara, Double Bay</p>
          <p>“Jess has helped to change my life around in all aspects. I would have been lost without her. Thanks Jess for your professionalism, support and guidance.” Elena, Cremorne</p>
          <p>“I was so busy with kids, work, and my husband I lost who I was. Jess has helped me find the person I am again.” Chloe, Chatswood</p>
          <p>“When I started with Coach Jess, I didn’t know anything about coaching. I called her because she helped a friend of mine make a career change that was a perfect fit for her. I had the opportunity to make a change too and did not know where to start. I am now in a job that I love. I would recommend Jess to everyone.” Daniel, Texas America</p>
        </div>
      </div>
      <div class="photo" role="img" aria-label="Photo of four happy friends jumping against a blue sky"></div>
      <svg class="shape" viewBox="0 0 269 570" preserveAspectRatio="none" aria-hidden="true" style="z-index:1">
        <path d="M0,430 C90,432 190,425 269,392 L269,412 C190,445 90,452 0,452 Z" fill="var(--green)"/>
        <path d="M0,0 L269,0 L269,392 C190,425 90,432 0,430 Z" fill="var(--paper)"/>
      </svg>
    </article>

    <article class="panel contact">
      <div class="content">
        <div class="intro">
          <p>Brightpath Coaching &amp; Meditation Studio is a professional service that can help you achieve the goals that you are looking for in Life Coaching, Meditation, and Yoga/Pilates.</p>
          <p>If you are ready to take your life to the next level and would like to know more, please</p>
        </div>
        <div class="brand"><span class="brand-dot"></span>Brightpath Coaching</div>
        <div class="details">
          <h3>contact us.</h3>
          <p>Phone : 02 9000 1234</p>
          <p>hello@brightpathcoaching.com.au</p>
          <p>www.brightpathcoaching.com.au</p>
        </div>
      </div>
      <div class="photo" role="img" aria-label="Portrait photo of the two coaches, a woman and a man"></div>
      <div class="offer">Free Introductory Life Coaching<br>Phone/Video session - 20 mins<br>(To see if coaching is right for you)</div>
    </article>

    <article class="panel cover">
      <div class="brand"><span class="brand-dot"></span>Brightpath Coaching</div>
      <svg class="shape" viewBox="0 0 269 570" preserveAspectRatio="none" role="img" aria-label="Photo of a couple doing a yoga pose by the sea">
        <defs>
          <linearGradient id="seaSky" x1="0" y1="0" x2="0" y2="1">
            <stop offset="0" stop-color="#9cc3dd"/>
            <stop offset="0.6" stop-color="#c9dbe6"/>
            <stop offset="1" stop-color="#6f9fbf"/>
          </linearGradient>
        </defs>
        <path d="M40,105 L269,105 L269,210 C200,290 110,300 40,262 C60,210 55,150 40,105 Z" fill="url(#seaSky)"/>
        <path d="M0,240 C10,250 25,256 40,262 C110,300 200,290 269,210 L269,570 L0,570 Z" fill="var(--blue)"/>
        <path d="M40,262 C110,300 200,290 269,210" fill="none" stroke="var(--green)" stroke-width="7"/>
      </svg>
      <div class="services">Life Coaching<br>Meditation<br>Yoga/Pilates</div>
    </article>
  </section>

  <section class="sheet sheet-inside" aria-label="Flyer inside">

    <article class="panel questions">
      <div class="content">
        <div class="asks">
          <p>Are you looking at making changes this year?</p>
          <p>Are you stuck in a rut or at a crossroad in your life?</p>
          <p>Are you wanting to lose weigh but can’t get motivated?</p>
          <p>Do you have ongoing problems with your career, relationships, or just life itself?</p>
          <p>Life coaching is the answer</p>
        </div>
        <h2 class="heading">Brightpath Coaching &amp; Meditation Studio</h2>
        <div class="body-text">
          <p>Our mission is to help you become the best possible person you can be. Mentally, physically, and spiritually.</p>
          <p>We offer highly qualified and compassionate trainers/coaches for Life Coaching, Meditation, Yoga and Pilates.</p>
          <p>They will guide and motivate you every step of the way to achieve all your dreams and goals.</p>
          <p>They will make you be the best you can be</p>
        </div>
      </div>
      <div class="photo" role="img" aria-label="Photo of a woman in a yoga balance pose by the sea"></div>
      <svg class="shape" viewBox="0 0 269 570" preserveAspectRatio="none" aria-hidden="true" style="z-index:1">
        <path d="M0,0 L269,0 L269,430 C180,438 90,440 0,436 Z" fill="var(--paper)"/>
        <path d="M0,436 C90,440 180,438 269,430 L269,452 C180,460 90,462 0,458 Z" fill="var(--green)"/>
      </svg>
    </article>

    <article class="panel services-panel">
      <div class="content">
        <h2 class="heading">Life Coaching</h2>
        <div class="body-text">
          <p>Your Life Coach will give you the confidence and the ability to move forward in a positive manner in all areas of your life where you crave change.</p>
          <p>Life Coaching is about breaking down the barriers preventing this change from happening, and creating the ideal environment for positive action to take place. It is a holistic approach, which looks at the present and sets goals for a totally successful future.</p>
        </div>
        <h2 class="heading">Career Coaching</h2>
        <div class="body-text">
          <p>Are you at a crossroads in your career and at a loss about what to do next? Do you want your work to be in alignment with the authentic you? It can be difficult to assess career options, goals, and strategies, and have the confidence to implement changes on your own. With the right coaching support, you will gain the clarity that you need to take control and have a fulfilling and rewarding career.</p>
        </div>
        <div class="brand"><span class="brand-dot"></span>Brightpath Coaching</div>
      </div>
      <div class="photo" role="img" aria-label="Photo of a smiling mother hugging her young daughter"></div>
      <svg class="shape" viewBox="0 0 269 570" preserveAspectRatio="none" aria-hidden="true" style="z-index:1">
        <path d="M0,0 L269,0 L269,402 C180,428 90,436 0,436 Z" fill="var(--paper)"/>
        <path d="M0,436 C90,436 180,428 269,402 L269,422 C180,450 90,458 0,458 Z" fill="var(--green)"/>
      </svg>
    </article>

    <article class="panel wellness">
      <svg class="shape" viewBox="0 0 269 570" preserveAspectRatio="none" aria-hidden="true">
        <defs>
          <linearGradient id="wellBlue" x1="0" y1="0" x2="1" y2="1">
            <stop offset="0" stop-color="#2a9ae0"/>
            <stop offset="1" stop-color="var(--blue-deep)"/>
          </linearGradient>
        </defs>
        <path d="M0,430 C150,420 240,310 269,170 L269,570 L0,570 Z" fill="url(#wellBlue)"/>
        <path d="M0,430 C150,420 240,310 269,170" fill="none" stroke="var(--green)" stroke-width="6"/>
      </svg>
      <div class="content">
        <h2 class="heading">Wellness Coaching</h2>
        <div class="body-text">
          <p>Health and wellness coaches help their clients find the motivation and tools to achieve their health and wellness goals, working with the client to examine and improve the psychological framework that supports those goals.</p>
        </div>
        <h2 class="heading">Why Would I Need Help?</h2>
        <div class="body-text">
          <p>Coaching is for anyone who wants to make lasting changes in their life. Coaching can assist with such issues as:</p>
        </div>
        <ul class="tick-list">
          <li><svg width="9" height="8" viewBox="0 0 9 8" aria-hidden="true"><path d="M1,4 L3.5,6.5 L8,1" fill="none" stroke="var(--green)" stroke-width="1.8"/></svg>Creating a better work- life balance</li>
          <li><svg width="9" height="8" viewBox="0 0 9 8" aria-hidden="true"><path d="M1,4 L3.5,6.5 L8,1" fill="none" stroke="var(--green)" stroke-width="1.8"/></svg>Resolving relationship issues</li>
          <li><svg width="9" height="8" viewBox="0 0 9 8" aria-hidden="true"><path d="M1,4 L3.5,6.5 L8,1" fill="none" stroke="var(--green)" stroke-width="1.8"/></svg>Career guidance</li>
          <li><svg width="9" height="8" viewBox="0 0 9 8" aria-hidden="true"><path d="M1,4 L3.5,6.5 L8,1" fill="none" stroke="var(--green)" stroke-width="1.8"/></svg>Stress management</li>
          <li><svg width="9" height="8" viewBox="0 0 9 8" aria-hidden="true"><path d="M1,4 L3.5,6.5 L8,1" fill="none" stroke="var(--green)" stroke-width="1.8"/></svg>Weight loss and fitness</li>
          <li><svg width="9" height="8" viewBox="0 0 9 8" aria-hidden="true"><path d="M1,4 L3.5,6.5 L8,1" fill="none" stroke="var(--green)" stroke-width="1.8"/></svg>Motivation and goal setting</li>
          <li><svg width="9" height="8" viewBox="0 0 9 8" aria-hidden="true"><path d="M1,4 L3.5,6.5 L8,1" fill="none" stroke="var(--green)" stroke-width="1.8"/></svg>Boosting your self esteem</li>
          <li><svg width="9" height="8" viewBox="0 0 9 8" aria-hidden="true"><path d="M1,4 L3.5,6.5 L8,1" fill="none" stroke="var(--green)" stroke-width="1.8"/></svg>Overcoming negative emotions &amp; thoughts</li>
          <li><svg width="9" height="8" viewBox="0 0 9 8" aria-hidden="true"><path d="M1,4 L3.5,6.5 L8,1" fill="none" stroke="var(--green)" stroke-width="1.8"/></svg>Better time management</li>
        </ul>
      </div>
      <div class="offerings">
        <h4>Meditation</h4>
        <p>We specialise in teaching meditation from beginners to advanced and teach a variety of techniques for stress reduction, peace of mind, stillness, and clarity.</p>
        <h4>Yoga/Pilates</h4>
        <p>Your highly qualified and experienced Yoga or Pilates instructor will come to you and create a fun and varied workout based on what you enjoy and what your goals are.</p>
      </div>
    </article>
  </section>

</main>
</body>
</html>
```